Pet Sitting Business Card

Would like a business card designed for my new pet sitting business
Card needs to match with logo design.
Blue and Orange are the theme colours.

Simple yet sophisticated design

company name:- MEADOWLARK PET CARE
Dana Kovich
Owner
0452716093
dana@meadowlarkpetcare.com.au
www.meadowlarkpetcare.com.au

I'm going to close my deadline early. I will be picking a winner by the 10th of May. Please submit designs before then.
thank you

Target Market(s)

All types of professional pet lovers wishing to have their pet looked after

Industry/Entity Type

Pet

Requirements
Must have
• Logo design
Blue and orange

```html
<!DOCTYPE html>
<html lang="en">
<head>
<meta charset="utf-8">
<title>Meadowlark Pet Care – Business Card</title>
<link href="https://fonts.googleapis.com/css2?family=Saira+Condensed:wght@500&family=Saira:wght@400;500;700&display=swap" rel="stylesheet">
<style>
  :root {
    --blue: #2f8ff0;
    --orange: #ea8a2b;
    --ink: #2a2a2a;
    --grey-light: #f6f6f6;
    --grey-mid: #c9c9c9;
    --paper: #ffffff;
    --backdrop: #e9ecef;
  }
  * { box-sizing: border-box; margin: 0; padding: 0; }
  html, body { width: 1200px; height: 877px; overflow: hidden; }
  body {
    background: var(--backdrop);
    font-family: "Saira", sans-serif;
    color: var(--ink);
    display: flex;
    align-items: center;
    justify-content: center;
    gap: 40px;
  }
  .card {
    position: relative;
    width: 540px;
    height: 309px;
    background: var(--paper);
    box-shadow: 0 10px 30px rgba(0,0,0,.15);
    overflow: hidden;
  }

  /* brand lockup */
  .brand {
    display: flex;
    align-items: center;
    gap: 8px;
    font-family: "Saira", sans-serif;
    font-weight: 700;
    color: var(--blue);
    line-height: 1.05;
  }
  .brand__dot {
    width: 14px; height: 14px; border-radius: 50%;
    background: var(--orange); flex: none;
  }

  /* back side */
  .card--back .logo-pill {
    position: absolute;
    left: 40px; top: 60px;
    width: 360px; height: 110px;
    border: 4px solid var(--orange);
    border-radius: 55px;
    background: linear-gradient(90deg, var(--grey-mid) 0%, var(--grey-light) 35%, var(--paper) 100%);
    display: flex; align-items: center; justify-content: center;
  }
  .card--back .brand { font-size: 22px; }
  .card--back .rule {
    position: absolute; left: 0; right: 0; top: 205px;
    height: 3px; background: var(--orange);
  }
  .card--back .band {
    position: absolute; left: 0; right: 0; top: 218px;
    height: 38px; background: var(--blue);
  }

  /* front side */
  .card--front .tab {
    position: absolute; width: 46px; height: 40px;
    background: var(--blue); border-radius: 3px;
  }
  .tab--left { left: -8px; top: 78px; }
  .tab--right { right: -8px; top: 110px; }
  .card--front .brand {
    position: absolute; left: 56px; top: 68px;
    font-size: 18px; width: 180px;
  }
  .person { position: absolute; left: 250px; top: 64px; }
  .person__name {
    font-family: "Saira Condensed", sans-serif;
    font-weight: 500; font-size: 44px; line-height: 1;
    letter-spacing: .5px;
    text-transform: uppercase;
  }
  .person__role { font-size: 12px; letter-spacing: .8px; margin-top: 4px; text-transform: uppercase; }
  .address {
    position: absolute; left: 20px; right: 70px; top: 162px;
    font-size: 14px; text-align: center;
  }
  .card--front .rule {
    position: absolute; left: 20px; right: 70px; top: 186px;
    height: 2px; background: var(--orange);
  }
  .divider {
    position: absolute; left: 240px; top: 206px;
    width: 2px; height: 62px; background: var(--orange);
  }
  .contact {
    position: absolute; list-style: none;
    font-size: 14px;
  }
  .contact li { display: flex; align-items: center; gap: 10px; height: 30px; }
  .contact svg { width: 20px; height: 20px; flex: none; }
  .contact--phones { left: 24px; top: 200px; }
  .contact--online { left: 264px; top: 218px; font-size: 12.5px; }
</style>
</head>
<body>

<section class="card card--back" aria-label="Card back">
  <div class="logo-pill">
    <div class="brand"><span class="brand__dot"></span><span>MEADOWLARK<br>PET CARE</span></div>
  </div>
  <div class="rule"></div>
  <div class="band"></div>
</section>

<section class="card card--front" aria-label="Card front">
  <div class="tab tab--left"></div>
  <div class="tab tab--right"></div>

  <div class="brand"><span class="brand__dot"></span><span>MEADOWLARK<br>PET CARE</span></div>

  <div class="person">
    <div class="person__name">Dana Kovich</div>
    <div class="person__role">Owner</div>
  </div>

  <p class="address">24 Wattle Grove Road, Suite 3, Kellerton</p>
  <div class="rule"></div>

  <ul class="contact contact--phones">
    <li>
      <svg viewBox="0 0 20 20"><circle cx="10" cy="10" r="9" fill="none" stroke="#2a2a2a" stroke-width="1.4"/><path d="M7 5.5c-.8.6-1 1.6-.6 2.8.7 2 2.4 3.9 4.4 4.9 1.1.5 2.1.4 2.8-.3l-1.6-1.6-1.1.6c-1-.5-1.9-1.4-2.4-2.4l.6-1.1z" fill="#2a2a2a"/></svg>
      <span>0452 716 093</span>
    </li>
    <li>
      <svg viewBox="0 0 20 20"><circle cx="10" cy="10" r="9" fill="none" stroke="#2a2a2a" stroke-width="1.4"/><rect x="7" y="4.5" width="6" height="11" rx="1" fill="none" stroke="#2a2a2a" stroke-width="1.3"/><circle cx="10" cy="13.5" r=".8" fill="#2a2a2a"/></svg>
      <span>0452 716 093</span>
    </li>
  </ul>

  <div class="divider"></div>

  <ul class="contact contact--online">
    <li>
      <svg viewBox="0 0 20 20"><circle cx="10" cy="10" r="9.5" fill="#2a2a2a"/><rect x="5" y="6.5" width="10" height="7" fill="none" stroke="#fff" stroke-width="1.2"/><path d="M5 6.5l5 4 5-4" fill="none" stroke="#fff" stroke-width="1.2"/></svg>
      <span>dana@meadowlarkpetcare.com.au</span>
    </li>
    <li>
      <svg viewBox="0 0 20 20"><circle cx="10" cy="10" r="9.5" fill="#2a2a2a"/><g fill="none" stroke="#fff" stroke-width="1"><circle cx="10" cy="10" r="5.5"/><ellipse cx="10" cy="10" rx="2.4" ry="5.5"/><path d="M4.5 10h11M5.5 7h9M5.5 13h9"/></g></svg>
      <span>www.meadowlarkpetcare.com.au</span>
    </li>
  </ul>
</section>

</body>
</html>
```